I want a website to be designed for our new company, it's an import and export company for variety of things.

please see the attached Logo for our company and the Images for our different sections for our busienss

Target Market(s)

multiple

Coding

Coded - Design and coding required

Number of Pages Required

5+ page

Font styles to use
Sans Serif

Colors

Designer to choose colors to be used in the design.

Requirements
Must have
• KVR GLOBALINKS
• KVR globalinks Trading & Contracting provides various services. The Company offers infrastructure construction, oil, enegy and gas services, agricultural projects, real estate development, travel and tourism, and food processing and trading.
• Civil contracting for infrastructure, residential and heavy projects. Through its main subsidiaries; distribution of general food products, construction chemicals including corrosion inhibitors and electrical machinery; provides catering and travel agency services; ownership and operation of a school; offers human sources services including manpower supply.
• Drilling and Gold Mines Used Machinery, All Kinds of Construction Machinery, Drilling Machines are manufactured and sold.
Nice to have
• good designa and beautiful colours, it has too look professional

```html
<!DOCTYPE html>
<html lang="en">
<head>
<meta charset="utf-8">
<title>KVR GLOBALINKS</title>
<link href="https://fonts.googleapis.com/css2?family=Raleway:wght@400;500;600;700;800&display=swap" rel="stylesheet">
<style>
:root{
  --orange:#f7941d;
  --dark:#252525;
  --darker:#1a1a1a;
  --text:#555;
  --white:#fff;
  --muted:#bdbdbd;
}
*{margin:0;padding:0;box-sizing:border-box}
html,body{width:1200px;height:4334px;overflow:hidden}
body{font-family:'Raleway',sans-serif;background:var(--white);color:var(--text);position:relative}
.abs{position:absolute}
.photo{position:absolute;display:block}
.btn{position:absolute;display:inline-flex;align-items:center;gap:8px;height:30px;padding:0 10px 0 11px;font-size:11px;font-weight:600;color:var(--white);text-transform:uppercase;letter-spacing:.2px}
.btn .dot{width:15px;height:15px;border-radius:50%;display:inline-flex;align-items:center;justify-content:center}
.btn-dark{background:#2b2b2b}
.btn-dark .dot{background:var(--orange)}
.btn-orange{background:var(--orange)}
.btn-orange .dot{background:#2b2b2b}

/* header */
.site-header{position:absolute;top:0;left:0;width:1200px;height:69px;background:var(--darker);z-index:3}
.brand{position:absolute;left:96px;top:22px;display:flex;align-items:center;gap:8px;color:var(--white);font-size:13px;font-weight:700;letter-spacing:.5px}
.brand i{width:16px;height:16px;border:none;background:var(--orange);border-radius:50%;display:block}
.nav{position:absolute;top:42px;left:690px;display:flex;font-size:12px;color:var(--white)}
.nav a{position:absolute;white-space:nowrap}
.nav .active{border-left:2px solid var(--orange);padding-left:6px}
.top-social{position:absolute;top:6px;left:1006px;display:flex;gap:7px}
.top-social span{width:20px;height:20px;border-radius:50%;background:#fff}
.top-social span:first-child{background:var(--orange)}

/* hero */
.hero{position:absolute;top:69px;left:0;width:1200px;height:531px;clip-path:polygon(0 0,100% 0,100% 100%,0 86%);background:#3a3530}
.hero-left{position:absolute;left:0;top:0;width:700px;height:531px;background:linear-gradient(180deg,#5a5146 0%,#6d6152 45%,#4a3f34 100%)}
.hero-right{position:absolute;left:560px;top:0;width:640px;height:531px;clip-path:polygon(25% 0,100% 0,100% 100%,0 100%);background:linear-gradient(135deg,#2b2b2b,#111)}
.hero-tool{position:absolute;left:860px;top:55px;width:330px;height:476px;background:radial-gradient(ellipse at 55% 40%,#e2372a 0%,#b52318 45%,rgba(30,30,30,0) 75%)}
.hero-copy{position:absolute;left:0;top:150px;width:1200px;text-align:center;color:var(--white)}
.hero-copy .kicker{font-size:58px;font-weight:800;color:var(--orange);line-height:1}
.hero-copy h1{font-size:68px;font-weight:800;line-height:1.1;letter-spacing:1px}
.hero-copy p{font-size:17px;font-weight:600;letter-spacing:6px;margin-top:12px}
.hero-dots{position:absolute;top:456px;left:579px;display:flex;gap:6px}
.hero-dots span{width:8px;height:8px;background:#fff}
.hero-dots span:first-child{background:var(--orange)}

/* welcome */
.welcome{position:absolute;top:600px;left:0;width:1200px;height:612px}
.welcome-shape{position:absolute;left:638px;top:85px;width:562px;height:370px;background:var(--orange);clip-path:polygon(0 0,100% 7%,100% 100%,0 100%)}
.eyebrow{font-size:23px;color:var(--orange);font-weight:400}
.section-title{font-size:39px;font-weight:800;color:#2b2b2b;line-height:1.1}
.welcome-copy{position:absolute;left:93px;top:133px;width:510px}
.welcome-copy p{font-size:13.5px;line-height:22.5px;margin-top:18px}

/* services */
.services{position:absolute;top:1212px;left:0;width:1200px;height:1038px;background:var(--dark);color:var(--white)}
.center-head{position:absolute;left:0;width:1200px;text-align:center}
.center-head .eyebrow{font-size:22px}
.center-head .section-title{color:var(--white);font-size:40px}
.center-head p{font-size:15px;color:#ddd;margin-top:6px}
.service-card{position:absolute;width:241px}
.service-card .photo{position:relative;width:241px;height:158px}
.service-card .label{font-size:14px;color:#ddd;margin-top:8px}
.service-card h3{font-size:21px;font-weight:600;line-height:1.1}
.service-card p{font-size:10.5px;line-height:18px;color:#bbb;margin-top:8px}
.service-card .btn{position:relative;margin-top:14px}
.view-all{position:absolute;left:517px;top:951px;width:168px;height:33px;background:#fff;color:#222;font-size:11px;font-weight:600;display:flex;align-items:center;justify-content:center}

/* machinery */
.machinery{position:absolute;top:2250px;left:0;width:1200px;height:694px}
.machinery-shape{position:absolute;left:0;top:86px;width:560px;height:336px;background:var(--orange)}
.machinery-copy{position:absolute;left:601px;top:86px;width:505px}
.machinery-copy .lead{font-size:17px;font-weight:700;color:#2b2b2b;line-height:25px;margin-top:14px}
.machinery-copy p{font-size:13.5px;line-height:22.5px;margin-top:14px}

/* news */
.news{position:absolute;top:2944px;left:0;width:1200px;height:599px;background:var(--dark);color:var(--white)}
.news-card{position:absolute;top:154px;width:324px}
.news-card .photo{position:relative;width:324px;height:201px}
.news-card h3{font-size:19px;font-weight:500;line-height:27px;margin-top:21px}
.news-card p{font-size:11px;line-height:19.5px;color:#bbb;margin-top:13px}
.news-card .btn{position:relative;margin-top:18px}

/* gallery */
.gallery{position:absolute;top:3543px;left:0;width:1200px;height:353px;display:grid;grid-template-columns:repeat(5,240px);grid-template-rows:repeat(2,176.5px)}
.gallery div{width:100%;height:100%}

/* footer */
.site-footer{position:absolute;top:3896px;left:0;width:1200px;height:438px;background:#fff}
.footer-col{position:absolute;top:88px}
.footer-col h4{font-size:18px;font-weight:500;color:#333}
.footer-col ul{list-style:none;margin-top:14px}
.footer-col li{font-size:11px;color:#555;height:29px;line-height:14px}
.footer-col li::before{content:"•";color:var(--orange);margin-right:3px}
.contact-line{display:flex;gap:8px;font-size:11px;color:#555;line-height:14px;margin-bottom:20px}
.contact-line svg{flex:none;margin-top:1px}
.field{width:243px;height:27px;border:1px solid #ccc;font-size:10px;color:#888;padding:0 10px;display:flex;align-items:center;margin-top:7px}
.subscribe{width:243px;height:29px;background:var(--orange);color:#fff;font-size:12px;display:flex;align-items:center;justify-content:center;margin-top:7px}
.copyright{position:absolute;top:291px;left:0;width:1200px;text-align:center;font-size:11.5px;color:#666;letter-spacing:.3px}
.copyright strong{color:#222;font-weight:600}
.foot-social{position:absolute;top:324px;left:532px;display:flex;gap:7px}
.foot-social span{width:30px;height:30px;border-radius:50%;border:1px solid #ccc}
.foot-social span:first-child{background:#222;border-color:#222}
</style>
</head>
<body>

<header class="site-header">
  <div class="brand"><i></i>KVR GLOBALINKS</div>
  <nav class="nav">
    <a class="active" style="left:0">Home</a>
    <a style="left:87px">About Us</a>
    <a style="left:185px">Services</a>
    <a style="left:278px">News</a>
    <a style="left:355px">Contact Us</a>
  </nav>
  <div class="top-social"><span></span><span></span><span></span><span></span></div>
</header>

<section class="hero">
  <div class="hero-left" role="img" aria-label="City skyline with twin towers above a large construction site"></div>
  <div class="hero-right"></div>
  <div class="hero-tool" role="img" aria-label="Red cordless power drill"></div>
  <div class="hero-copy">
    <div class="kicker">KVR</div>
    <h1>GLOBALINKS</h1>
    <p>A LARGE ASSORTMENT</p>
  </div>
  <div class="hero-dots"><span></span><span></span><span></span></div>
</section>

<section class="welcome">
  <div class="welcome-shape"></div>
  <div class="photo" style="left:714px;top:145px;width:392px;height:379px;background:linear-gradient(160deg,#4f5d68,#7d7a6c 50%,#2e3a44)" role="img" aria-label="Two engineers in hard hats shaking hands"></div>
  <div class="welcome-copy">
    <div class="eyebrow">Welcome To</div>
    <h2 class="section-title">KVR GLOBALINKS</h2>
    <p>Sed ut perspiciatis unde omnis iste natus error sit voluptatem accusantium doloremque laudantium, totam rem aperiam, eaque ipsa quae ab illo inventore veritatis et quasi architecto beatae vitae dicta sunt explicabo. Nemo enim ipsam voluptatem quia voluptas sit aspernatur aut odit aut fugit, sed quia consequuntur magni dolores eos qui ratione voluptatem sequi nesciunt. Neque porro quisquam est, qui dolorem ipsum quia dolor sit amet, consectetur, adipisci velit, sed quia non numquam eius modi tempora incidunt ut labore et dolore magnam aliquam quaerat voluptatem.</p>
  </div>
  <a class="btn btn-dark" style="left:93px;top:441px">Read More <span class="dot"><svg width="6" height="8" viewBox="0 0 6 8"><path d="M1 1l3 3-3 3" stroke="#fff" stroke-width="1.5" fill="none"/></svg></span></a>
</section>

<section class="services">
  <div class="center-head" style="top:64px">
    <div class="eyebrow">KVR globalinks</div>
    <h2 class="section-title">OUR SERVICES</h2>
    <p>KVR globalinks Trading &amp; Contracting provides various services</p>
  </div>

  <article class="service-card" style="left:93px;top:210px">
    <div class="photo" style="background:linear-gradient(180deg,#3d84c6,#8fb4d3 55%,#c46a2c)" role="img" aria-label="Orange excavator at a work site"></div>
    <div class="label">Infrastructure</div><h3>Construction</h3>
    <p>But I must explain to you how all this mistaken idea of denouncing pleasure and praising pain...</p>
    <a class="btn btn-orange">Read More <span class="dot"><svg width="6" height="8" viewBox="0 0 6 8"><path d="M1 1l3 3-3 3" stroke="#fff" stroke-width="1.5" fill="none"/></svg></span></a>
  </article>
  <article class="service-card" style="left:351px;top:210px">
    <div class="photo" style="background:linear-gradient(180deg,#2f6fc0,#6a8fb5 50%,#3d3f44)" role="img" aria-label="Gas refinery towers against a blue sky"></div>
    <div class="label">Enegy and</div><h3>Gas Services</h3>
    <p>But I must explain to you how all this mistaken idea of denouncing pleasure and praising pain...</p>
    <a class="btn btn-orange">Read More <span class="dot"><svg width="6" height="8" viewBox="0 0 6 8"><path d="M1 1l3 3-3 3" stroke="#fff" stroke-width="1.5" fill="none"/></svg></span></a>
  </article>
  <article class="service-card" style="left:608px;top:210px">
    <div class="photo" style="background:linear-gradient(180deg,#9fb3c4,#c9c6b5 45%,#6b7a3e)" role="img" aria-label="Combine harvester and tractor in a field"></div>
    <div class="label">Agricultural</div><h3>Projects</h3>
    <p>But I must explain to you how all this mistaken idea of denouncing pleasure and praising pain...</p>
    <a class="btn btn-orange">Read More <span class="dot"><svg width="6" height="8" viewBox="0 0 6 8"><path d="M1 1l3 3-3 3" stroke="#fff" stroke-width="1.5" fill="none"/></svg></span></a>
  </article>
  <article class="service-card" style="left:865px;top:210px">
    <div class="photo" style="background:linear-gradient(180deg,#3f8de0,#7db3e8 60%,#8a5a3a)" role="img" aria-label="Tower crane over a building under construction"></div>
    <div class="label">Real Estate</div><h3>Development</h3>
    <p>But I must explain to you how all this mistaken idea of denouncing pleasure and praising pain...</p>
    <a class="btn btn-orange">Read More <span class="dot"><svg width="6" height="8" viewBox="0 0 6 8"><path d="M1 1l3 3-3 3" stroke="#fff" stroke-width="1.5" fill="none"/></svg></span></a>
  </article>

  <article class="service-card" style="left:93px;top:560px">
    <div class="photo" style="background:linear-gradient(180deg,#d8dcd6,#9ca39a 55%,#5e6559)" role="img" aria-label="Traveller pulling a suitcase through an airport"></div>
    <div class="label">Travel and</div><h3>Tourism</h3>
    <p>But I must explain to you how all this mistaken idea of denouncing pleasure and praising pain...</p>
    <a class="btn btn-orange">Read More <span class="dot"><svg width="6" height="8" viewBox="0 0 6 8"><path d="M1 1l3 3-3 3" stroke="#fff" stroke-width="1.5" fill="none"/></svg></span></a>
  </article>
  <article class="service-card" style="left:351px;top:560px">
    <div class="photo" style="background:linear-gradient(160deg,#6b5a44,#c8ae86 50%,#3a3128)" role="img" aria-label="Potatoes on a food processing line"></div>
    <div class="label">Food</div><h3>Processing</h3>
    <p>But I must explain to you how all this mistaken idea of denouncing pleasure and praising pain...</p>
    <a class="btn btn-orange">Read More <span class="dot"><svg width="6" height="8" viewBox="0 0 6 8"><path d="M1 1l3 3-3 3" stroke="#fff" stroke-width="1.5" fill="none"/></svg></span></a>
  </article>
  <article class="service-card" style="left:608px;top:560px">
    <div class="photo" style="background:linear-gradient(180deg,#6d7c92,#e0a168 50%,#4a5a6e)" role="img" aria-label="Offshore oil platform at sunset"></div>
    <div class="label">Oil</div><h3>Industries</h3>
    <p>But I must explain to you how all this mistaken idea of denouncing pleasure and praising pain...</p>
    <a class="btn btn-orange">Read More <span class="dot"><svg width="6" height="8" viewBox="0 0 6 8"><path d="M1 1l3 3-3 3" stroke="#fff" stroke-width="1.5" fill="none"/></svg></span></a>
  </article>
  <article class="service-card" style="left:865px;top:560px">
    <div class="photo" style="background:linear-gradient(180deg,#8d959b,#5a5f63 50%,#2f3337)" role="img" aria-label="Group of workers in yellow hard hats"></div>
    <div class="label">Human</div><h3>Sources Services</h3>
    <p>But I must explain to you how all this mistaken idea of denouncing pleasure and praising pain...</p>
    <a class="btn btn-orange">Read More <span class="dot"><svg width="6" height="8" viewBox="0 0 6 8"><path d="M1 1l3 3-3 3" stroke="#fff" stroke-width="1.5" fill="none"/></svg></span></a>
  </article>

  <a class="view-all">VIEW ALL SERVICES</a>
</section>

<section class="machinery">
  <div class="machinery-shape"></div>
  <div class="photo" style="left:76px;top:145px;width:390px;height:461px;background:linear-gradient(170deg,#e8dcb8,#c9b27a 50%,#6e5a35)" role="img" aria-label="Mining dump trucks in a dusty open-pit mine"></div>
  <div class="photo" style="left:473px;top:451px;width:207px;height:155px;background:linear-gradient(160deg,#7b6a55,#3f3429)" role="img" aria-label="Underground mining loader"></div>
  <div class="photo" style="left:685px;top:451px;width:207px;height:155px;background:linear-gradient(160deg,#6d7784,#2d3138)" role="img" aria-label="Drilling machinery inside a mine tunnel"></div>
  <div class="photo" style="left:899px;top:451px;width:207px;height:155px;background:linear-gradient(180deg,#c9d6dc,#6b7a4a 50%,#8a6a45)" role="img" aria-label="Gold mining site cleared in a forest"></div>
  <div class="machinery-copy">
    <div class="eyebrow">Drilling and Gold Mines</div>
    <h2 class="section-title">USED MACHINERY</h2>
    <div class="lead">All Kinds of Construction Machinery, Drilling Machines are manufactured and sold.</div>
    <p>Sed ut perspiciatis unde omnis iste natus error sit voluptatem accusantium doloremque laudantium, totam rem aperiam, eaque ipsa quae ab illo inventore veritatis et quasi architecto beatae vitae dicta sunt explicabo. Nemo enim ipsam voluptatem quia voluptas sit aspernatur aut odit aut fugit, sed quia consequuntur magni dolores eos qui ratione voluptatem sequi nesciunt. Neque porro quisquam est, qui dolorem ipsum</p>
  </div>
  <a class="btn btn-dark" style="left:601px;top:392px">Read More <span class="dot"><svg width="6" height="8" viewBox="0 0 6 8"><path d="M1 1l3 3-3 3" stroke="#fff" stroke-width="1.5" fill="none"/></svg></span></a>
</section>

<section class="news">
  <div class="center-head" style="top:66px">
    <div class="eyebrow">KVR globalinks</div>
    <h2 class="section-title">LATEST NEWS</h2>
  </div>
  <article class="news-card" style="left:93px">
    <div class="photo" style="background:linear-gradient(90deg,#5a3e26,#b98a55 50%,#4a3320)" role="img" aria-label="Business meeting at a table"></div>
    <h3>There are many variations passages Lorem Ipsum</h3>
    <p>If you use this site regularly and would like to help keep the site on the Internet, please consider donating a small sum to help pay</p>
    <a class="btn btn-orange">Read More <span class="dot"><svg width="6" height="8" viewBox="0 0 6 8"><path d="M1 1l3 3-3 3" stroke="#fff" stroke-width="1.5" fill="none"/></svg></span></a>
  </article>
  <article class="news-card" style="left:438px">
    <div class="photo" style="background:linear-gradient(160deg,#9aa6ae,#dfe3e4 50%,#5c6a72)" role="img" aria-label="Laptop, coffee and plant on a meeting table"></div>
    <h3>There are many variations passages Lorem Ipsum</h3>
    <p>If you use this site regularly and would like to help keep the site on the Internet, please consider donating a small sum to help pay</p>
    <a class="btn btn-orange">Read More <span class="dot"><svg width="6" height="8" viewBox="0 0 6 8"><path d="M1 1l3 3-3 3" stroke="#fff" stroke-width="1.5" fill="none"/></svg></span></a>
  </article>
  <article class="news-card" style="left:783px">
    <div class="photo" style="background:linear-gradient(180deg,#d7dde2,#a9b0a8 55%,#7d7556)" role="img" aria-label="Engineers reviewing plans at a construction site"></div>
    <h3>There are many variations passages Lorem Ipsum</h3>
    <p>If you use this site regularly and would like to help keep the site on the Internet, please consider donating a small sum to help pay</p>
    <a class="btn btn-orange">Read More <span class="dot"><svg width="6" height="8" viewBox="0 0 6 8"><path d="M1 1l3 3-3 3" stroke="#fff" stroke-width="1.5" fill="none"/></svg></span></a>
  </article>
</section>

<section class="gallery">
  <div style="background:linear-gradient(180deg,#6d7c92,#e0a168 50%,#4a5a6e)" role="img" aria-label="Offshore platform at sunset"></div>
  <div style="background:linear-gradient(160deg,#8fa3b0,#506270)" role="img" aria-label="Forestry machine in a misty forest"></div>
  <div style="background:linear-gradient(180deg,#c8ccd0,#8d9399)" role="img" aria-label="Aerial view of an industrial complex"></div>
  <div style="background:linear-gradient(180deg,#3f8de0,#7db3e8 60%,#8a5a3a)" role="img" aria-label="Tower crane over a building"></div>
  <div style="background:linear-gradient(180deg,#8d959b,#5a5f63 50%,#2f3337)" role="img" aria-label="Workers in hard hats"></div>
  <div style="background:linear-gradient(180deg,#d8dcd6,#9ca39a 55%,#5e6559)" role="img" aria-label="Traveller in an airport terminal"></div>
  <div style="background:linear-gradient(180deg,#3d84c6,#8fb4d3 55%,#c46a2c)" role="img" aria-label="Orange excavator"></div>
  <div style="background:linear-gradient(180deg,#e4e8e2,#7fae4a)" role="img" aria-label="Rows of lettuce seedlings"></div>
  <div style="background:linear-gradient(180deg,#5d8aa6,#2f5a73)" role="img" aria-label="Offshore drilling rig from above"></div>
  <div style="background:linear-gradient(180deg,#2f6fc0,#6a8fb5 50%,#3d3f44)" role="img" aria-label="Gas refinery towers"></div>
</section>

<footer class="site-footer">
  <div class="footer-col" style="left:93px">
    <h4>Quick Links</h4>
    <ul><li>Home</li><li>About Us</li><li>Services</li><li>News</li><li>Contact Us</li></ul>
  </div>
  <div class="footer-col" style="left:259px">
    <h4>Services</h4>
    <ul><li>Construction</li><li>Oil Industry</li><li>Enegy &amp; gas services</li><li>Agricultural Projects</li></ul>
  </div>
  <div class="footer-col" style="left:410px">
    <h4>&nbsp;</h4>
    <ul><li>Real Estate Development</li><li>Travel &amp; Tourism</li><li>Food Processing</li><li>Human Sources Services</li></ul>
  </div>
  <div class="footer-col" style="left:635px">
    <h4>Contact Us</h4>
    <div style="margin-top:14px">
      <div class="contact-line"><svg width="10" height="13" viewBox="0 0 10 13"><path d="M5 0a5 5 0 0 1 5 5c0 3.5-5 8-5 8S0 8.5 0 5a5 5 0 0 1 5-5z" fill="#f7941d"/><circle cx="5" cy="5" r="1.8" fill="#fff"/></svg><span>42 Harbour Row,<br>Brightwater 4100</span></div>
      <div class="contact-line"><svg width="11" height="11" viewBox="0 0 11 11"><path d="M2 0l2 2.5-1.2 1.5a7 7 0 0 0 4.2 4.2L8.5 7 11 9l-1.5 2C4.5 11 0 6.5 0 1.5z" fill="#f7941d"/></svg><span>+1 (555) 274 6190</span></div>
      <div class="contact-line"><svg width="11" height="9" viewBox="0 0 11 9"><rect width="11" height="9" fill="#f7941d"/><path d="M0 0l5.5 4.5L11 0" stroke="#fff" fill="none"/></svg><span>hello@kvrglobalinks.com</span></div>
    </div>
  </div>
  <div class="footer-col" style="left:863px">
    <h4>Newsletter</h4>
    <div style="margin-top:11px">
      <div class="field">Enter Name:</div>
      <div class="field">Enter Email:</div>
      <div class="subscribe">Subscribe</div>
    </div>
  </div>
  <div class="copyright">COPYRIGHT © 2020 <strong>KVR GLOBALINKS</strong>. ALL RIGHTS RESERVED.</div>
  <div class="foot-social"><span></span><span></span><span></span><span></span></div>
</footer>

</body>
</html>
```